Business Card Design needed for start up company Halvora

In need of a new business card designed for a start up company based in Sydney, Halvora is a new start up innovative Company, our mission it to make property accessible for everyday Australian and to become the leading Real Estate platform in Australia. We want it to be fresh and clean.

Industry/Entity Type

Financial

Contact Information for Business Card

Section for Name
Section for Title

HALVORA - The Strength of Pooling
Mobile:
Direct:

Font styles to use
Sans Serif

Colors
33a6d7
0692cd
0255a3
ffffff

Requirements
Must have
• Logo, all business card details

```html
<!DOCTYPE html>
<html lang="en">
<head>
<meta charset="utf-8">
<title>Halvora Business Card</title>
<link rel="stylesheet" href="https://fonts.googleapis.com/css2?family=Open+Sans:wght@400;600;700&display=swap">
<style>
  :root {
    --navy: #2443a3;
    --sky: #33a6d7;
    --sky-light: #5bbdea;
    --white: #ffffff;
    --ink: #3a3a3a;
    --rule: #9a9a9a;
    --stage: #1f2022;
  }
  * { margin: 0; padding: 0; box-sizing: border-box; }
  html, body { width: 1200px; height: 1000px; overflow: hidden; }
  body {
    background: var(--stage);
    font-family: "Open Sans", Arial, sans-serif;
    position: relative;
  }
  .card {
    position: absolute;
    left: 250px;
    width: 700px;
    height: 400px;
    border-radius: 34px;
    overflow: hidden;
  }
  .card--front {
    top: 60px;
    background: linear-gradient(45deg, var(--navy) 0%, #3478c8 50%, var(--sky-light) 100%);
  }
  .card--back { top: 540px; background: var(--white); }

  .brand-name {
    position: absolute;
    font-weight: 600;
    line-height: 1;
    letter-spacing: 6px;
  }
  .card--front .brand-name {
    left: 0; right: 0; top: 168px;
    text-align: center;
    font-size: 56px;
    color: var(--white);
  }
  .tagline {
    position: absolute; bottom: 40px; left: 0; right: 0;
    text-align: center; color: var(--white);
    font-size: 13px; letter-spacing: 5px; font-weight: 600;
  }

  .card--back .brand-name {
    left: 40px; top: 92px;
    font-size: 44px;
    color: var(--navy);
  }
  .divider { position: absolute; left: 40px; top: 215px; width: 400px; height: 1px; background: var(--rule); }

  .person { position: absolute; right: 40px; top: 38px; text-align: right; }
  .person__name {
    font-size: 27px; font-weight: 700; color: var(--navy);
    padding-bottom: 2px; border-bottom: 3px solid var(--navy);
    letter-spacing: 0.3px;
  }
  .person__title { font-size: 19px; color: var(--sky); margin-top: 2px; }

  .contacts { position: absolute; right: 40px; top: 140px; list-style: none; }
  .contacts li { font-size: 17px; color: var(--ink); line-height: 24px; display: flex; justify-content: flex-end; align-items: center; gap: 10px; }
  .contacts svg { width: 14px; height: 14px; fill: var(--navy); }

  .address { position: absolute; left: 40px; top: 290px; display: flex; gap: 10px; font-size: 17px; color: var(--ink); line-height: 23px; }
  .address svg { width: 16px; height: 16px; fill: var(--sky); margin-top: 2px; flex: none; }

  .bands { position: absolute; left: 0; bottom: 0; width: 700px; height: 120px; }
  .website { position: absolute; right: 40px; bottom: 20px; color: var(--white); font-size: 17px; line-height: 24px; }
</style>
</head>
<body>
  <section class="card card--front" aria-label="Card front">
    <p class="brand-name">HALVORA</p>
    <p class="tagline">THE STRENGTH OF POOLING</p>
  </section>

  <section class="card card--back" aria-label="Card back">
    <p class="brand-name">HALVORA</p>
    <div class="divider"></div>

    <div class="person">
      <p class="person__name">MARCUS REID</p>
      <p class="person__title">Director</p>
    </div>

    <ul class="contacts">
      <li>000 481 905 276
        <svg viewBox="0 0 24 24"><path d="M6.6 10.8a15 15 0 0 0 6.6 6.6l2.2-2.2a1 1 0 0 1 1-.25 11.4 11.4 0 0 0 3.6.57 1 1 0 0 1 1 1V20a1 1 0 0 1-1 1A17 17 0 0 1 3 4a1 1 0 0 1 1-1h3.5a1 1 0 0 1 1 1c0 1.25.2 2.45.57 3.6a1 1 0 0 1-.25 1z"/></svg></li>
      <li>000 739 6150
        <svg viewBox="0 0 24 24"><path d="M7 1h10a2 2 0 0 1 2 2v18a2 2 0 0 1-2 2H7a2 2 0 0 1-2-2V3a2 2 0 0 1 2-2zm0 3v14h10V4zm5 15.5a1 1 0 1 0 0 2 1 1 0 0 0 0-2z"/></svg></li>
      <li>hello@halvora.com
        <svg viewBox="0 0 24 24"><path d="M2 5h20v14H2zm2 2v.5l8 5 8-5V7z"/></svg></li>
    </ul>

    <p class="address">
      <svg viewBox="0 0 24 24"><path d="M2 21 23 12 2 3v7l15 2-15 2z"/></svg>
      <span>Your Street Address,<br>Sydney, 2000</span>
    </p>

    <svg class="bands" viewBox="0 0 700 120" aria-hidden="true">
      <path d="M0,100 L372,100 L392,56 L700,56 L700,64 L396,64 L376,108 L0,108 Z" fill="var(--sky)"/>
      <path d="M0,108 L376,108 L396,64 L700,64 L700,120 L0,120 Z" fill="var(--navy)"/>
    </svg>
    <p class="website">www.halvora.com</p>
  </section>
</body>
</html>
```